Quorva - corporate Business Card

We need a good look and innovative business card for a new start up company based in Los Angeles called "Quorva". We are in a payment business, including payment card, app, and ewallet. We are expert in online payment and Card not present (CNP) transaction.
We need an innovative, modern business card.

Our logo font is Aero Matics

Target Market(s)

Startup - Bank - Online Payment - Card Manufacturing

Industry/Entity Type

Startup

Contact Information for Business Card

phone: 555 014 7396 - Address: 4172 Marlowe blvd, Halvern City, CA 90299

Requirements
Must have
• Message: innovative, professional, expert, high tech, trust, online payment expert, security
Nice to have
• no comment
Should not have
• no Comment

```html
<!DOCTYPE html>
<html lang="en">
<head>
<meta charset="utf-8">
<title>Quorva – Business Card</title>
<link href="https://fonts.googleapis.com/css2?family=Open+Sans:wght@400;600;700&display=swap" rel="stylesheet">
<style>
  :root {
    --backdrop: #3a3430;
    --card: #0d0d0d;
    --card-edge: #1c1c1c;
    --accent-red: #c41e2e;
    --text-light: #eeeeee;
    --silver: #c9c9c9;
    --silver-disc: #e6e6e6;
  }
  * { margin: 0; padding: 0; box-sizing: border-box; }
  html, body {
    width: 1200px; height: 900px; overflow: hidden;
    background: var(--backdrop);
    font-family: "Open Sans", Arial, sans-serif;
  }
  .canvas {
    position: relative; width: 1200px; height: 900px;
    display: flex; align-items: center; justify-content: center; gap: 40px;
  }
  .card {
    position: relative; width: 525px; height: 300px;
    background: var(--card);
    border: 1px solid var(--card-edge);
    box-shadow: 0 10px 30px rgba(0,0,0,.45);
  }
  /* Contact side */
  .brand-disc {
    position: absolute; left: 70px; top: 85px;
    width: 130px; height: 130px; border-radius: 50%;
    background: var(--accent-red);
    display: flex; align-items: center; justify-content: center;
  }
  .brand-disc .brand-name {
    color: var(--text-light); font-weight: 700; font-size: 22px; letter-spacing: .5px;
  }
  .divider {
    position: absolute; left: 262px; top: 80px; width: 1px; height: 140px;
    background: linear-gradient(to bottom, var(--accent-red), rgba(196,30,46,0));
  }
  .contact { position: absolute; left: 282px; top: 78px; color: var(--text-light); }
  .person-name {
    color: var(--accent-red); font-weight: 700; font-size: 17px; letter-spacing: .3px;
    text-transform: uppercase; line-height: 1.1;
  }
  .person-title { font-size: 12.5px; margin-bottom: 14px; }
  .contact-line { display: flex; align-items: center; gap: 8px; font-size: 12.5px; line-height: 1.6; }
  .contact-line svg { width: 10px; height: 10px; flex: none; }
  .address { font-size: 12.5px; line-height: 1.45; margin-top: 8px; }
  /* Brand side */
  .brand-lockup {
    position: absolute; inset: 0;
    display: flex; align-items: center; justify-content: center; gap: 16px;
  }
  .brand-lockup .disc {
    width: 78px; height: 78px; border-radius: 50%; background: var(--silver-disc);
  }
  .brand-lockup .wordmark {
    color: var(--silver); font-weight: 600; font-size: 56px; letter-spacing: 1px;
    text-transform: lowercase;
  }
</style>
</head>
<body>
<main class="canvas">
  <section class="card card--contact">
    <div class="brand-disc"><span class="brand-name">Quorva</span></div>
    <div class="divider"></div>
    <div class="contact">
      <p class="person-name">Daniel Harrow</p>
      <p class="person-title">Managing Director</p>
      <p class="contact-line">
        <svg viewBox="0 0 10 10" aria-hidden="true"><path d="M2 0.5 L3.6 2.6 L2.8 3.6 Q4 6 6.4 7.2 L7.4 6.4 L9.5 8 L8.3 9.5 Q1 8 0.5 1.7 Z" fill="var(--accent-red)"/></svg>
        555 014 7396
      </p>
      <p class="contact-line">
        <svg viewBox="0 0 10 10" aria-hidden="true"><circle cx="5" cy="5" r="4.5" fill="var(--accent-red)"/></svg>
        www.quorva.com
      </p>
      <p class="address">4172 Marlowe blvd,<br>Halvern City, CA 90299</p>
    </div>
  </section>
  <section class="card card--brand">
    <div class="brand-lockup">
      <span class="disc"></span>
      <span class="wordmark">quorva</span>
    </div>
  </section>
</main>
</body>
</html>
```